Harrow grounds and gardens

Lawn Maintenance, Spring Fall Clean Ups, Stone Walls & Walkways, Commercial and Residental Snow Removal carpentry and handyman services

Industry/Entity Type

Carpentry

Contact Information for Business Card

Harrow Grounds and Gardens 83 Pebble Marsh Rd Fernvale NY 10999 555 261 3087 Cell 555319 5402

```html
<!DOCTYPE html>
<html lang="en">
<head>
<meta charset="utf-8">
<title>Harrow Grounds and Gardens – Business Card</title>
<link href="https://fonts.googleapis.com/css2?family=Ubuntu:wght@400;500;700&display=swap" rel="stylesheet">
<style>
  :root {
    --page-bg: #e9e6e1;
    --card-white: #ffffff;
    --card-shade: #eeeeee;
    --brand-green: #5cb247;
    --band-light: #7cc766;
    --band-dark: #4fa33e;
    --text-white: #ffffff;
  }
  * { margin: 0; padding: 0; box-sizing: border-box; }
  html, body {
    width: 1200px; height: 818px; overflow: hidden;
    background: var(--page-bg);
    font-family: "Ubuntu", sans-serif;
  }
  .card {
    position: absolute;
    left: 75px; top: 109px;
    width: 1050px; height: 600px;
    background: linear-gradient(180deg, var(--card-white), var(--card-shade));
    box-shadow: 0 10px 30px rgba(0,0,0,0.18);
    overflow: hidden;
  }
  .brand {
    position: absolute;
    left: 0; right: 0; top: 40px;
    display: flex; align-items: center; justify-content: center;
    gap: 18px;
    color: var(--brand-green);
    font-weight: 700;
  }
  .brand-dot {
    width: 46px; height: 46px; border-radius: 50%;
    background: var(--brand-green);
  }
  .brand-text { line-height: 1; }
  .brand-name { font-size: 78px; letter-spacing: -1px; display: block; }
  .brand-sub { font-size: 36px; display: block; margin-top: 6px; }
  .band {
    position: absolute;
    left: 0; right: 0; top: 200px; height: 300px;
    background: linear-gradient(180deg, var(--band-light), var(--band-dark));
    color: var(--text-white);
    text-align: center;
    padding-top: 34px;
  }
  .person { font-size: 44px; font-weight: 700; }
  .phones { margin-top: 14px; font-size: 28px; line-height: 1.4; }
  .phone-line { display: flex; align-items: center; justify-content: center; gap: 14px; }
  .phone-icon { width: 24px; height: 24px; }
  .services { margin-top: 20px; font-size: 27px; line-height: 1.4; }
  .address {
    position: absolute;
    left: 0; right: 0; top: 525px;
    text-align: center;
    color: var(--brand-green);
    font-size: 30px;
    font-weight: 500;
  }
</style>
</head>
<body>
  <div class="card">
    <div class="brand">
      <span class="brand-dot"></span>
      <span class="brand-text">
        <span class="brand-name">Harrow</span>
        <span class="brand-sub">Grounds and Gardens</span>
      </span>
    </div>

    <div class="band">
      <div class="person">Tom Harrow</div>
      <div class="phones">
        <div class="phone-line">
          <span>555319 5402</span>
          <svg class="phone-icon" viewBox="0 0 24 24" aria-label="Office phone">
            <rect x="1" y="1" width="22" height="22" rx="2" fill="#fff"/>
            <rect x="5" y="4" width="14" height="6" fill="#5cb247"/>
            <rect x="5" y="13" width="14" height="7" fill="#5cb247"/>
          </svg>
        </div>
        <div class="phone-line">
          <span>555 261 3087</span>
          <svg class="phone-icon" viewBox="0 0 24 24" aria-label="Mobile phone">
            <rect x="1" y="1" width="22" height="22" rx="2" fill="#fff"/>
            <rect x="8" y="4" width="8" height="16" rx="1.5" fill="#5cb247"/>
            <rect x="9.5" y="6" width="5" height="9" fill="#fff"/>
          </svg>
        </div>
      </div>
      <div class="services">
        Commercial and Residential Snow Removal<br>
        Carpentry and Handyman Services
      </div>
    </div>

    <div class="address">83 Pebble Marsh Rd Fernvale NY 10999</div>
  </div>
</body>
</html>
```